Redesign of Form/Document Navigation Page

I need a redesign of our document and navigation bar on the left. We want the same navigation bar layout/setup but want the buttons and typography to be simple and matching all over. The form needs to be aesthetically pleasing and fit within the page.

1st attachment is our Direct Deposit and the second is the form continued.

```html
<!DOCTYPE html>
<html lang="en">
<head>
<meta charset="utf-8">
<title>Employee Direct Deposit Enrollment Form</title>
<link rel="stylesheet" href="https://fonts.googleapis.com/css2?family=Open+Sans:wght@400;600&family=Roboto:wght@400;500&display=swap">
<style>
  :root{
    --blue:#2c63ad;
    --blue-dark:#25589d;
    --yellow:#f7df73;
    --gold:#e8b21d;
    --page:#ebebeb;
    --text:#222;
    --line:#c9c9c9;
    --white:#fff;
  }
  *{box-sizing:border-box;margin:0;padding:0}
  html,body{width:1165px;height:1200px;overflow:hidden}
  body{background:var(--page);font-family:"Open Sans",sans-serif;color:var(--text);position:relative}

  .site-header{position:absolute;left:0;top:0;width:1165px;height:103px;background:var(--white);border-bottom:2px solid var(--blue)}
  .brand{position:absolute;left:96px;top:36px;display:flex;align-items:center;gap:10px}
  .brand-dot{width:32px;height:32px;border-radius:50%;background:var(--gold)}
  .brand-name{font-family:"Roboto",sans-serif;font-weight:500;font-size:20px;line-height:21px;color:var(--gold);letter-spacing:.2px}
  .top-nav{position:absolute;right:97px;top:43px;display:flex;align-items:center;font-family:"Roboto",sans-serif;font-size:14px;color:#111}
  .top-nav .sep{margin:0 20px}
  .top-nav .user{margin-left:38px;margin-right:10px}
  .power{width:28px;height:28px;border-radius:50%;background:var(--blue);display:flex;align-items:center;justify-content:center}

  .side-nav{position:absolute;left:95px;top:143px;width:251px;background:var(--white);border:2px solid #e4e4e4;padding:0}
  .side-nav a{display:flex;align-items:center;height:53px;margin-bottom:2px;background:var(--blue);color:var(--white);text-decoration:none;font-family:"Roboto",sans-serif;font-weight:500;font-size:16.5px;padding-left:13px}
  .side-nav a:last-child{margin-bottom:0}
  .side-nav a.back{background:var(--yellow);color:var(--blue);height:54px;font-weight:400;font-size:16.5px;padding-left:14px}
  .side-nav a.back svg{margin-right:9px}
  .nav-icon{width:32px;height:32px;border-radius:50%;background:var(--yellow);display:flex;align-items:center;justify-content:center;margin-right:12px}

  .form-panel{position:absolute;left:361px;top:143px;width:709px;height:971px;background:var(--white);border:1px solid #dcdcdc;overflow:hidden}
  .scrollbar{position:absolute;right:0;top:0;width:17px;height:100%;background:#f0f0f0}
  .scrollbar .thumb{position:absolute;left:3px;top:25px;width:10px;height:235px;background:#c1c1c1}
  .scrollbar .up,.scrollbar .down{position:absolute;left:4px;width:0;height:0;border-left:4px solid transparent;border-right:4px solid transparent}
  .scrollbar .up{top:7px;border-bottom:5px solid #888}
  .scrollbar .down{bottom:7px;border-top:5px solid #888}

  .form-body{padding:28px 20px 0 15px;width:692px}
  .form-title{font-family:"Roboto",sans-serif;font-weight:500;font-size:21px;color:var(--blue);text-align:center;line-height:26px}
  .title-rule{width:202px;height:2px;background:var(--blue);margin:17px auto 0}
  .intro{font-size:12.6px;line-height:21.6px;text-align:center;margin-top:22px}
  .intro + .intro{margin-top:8px}

  .attach-box{margin-top:21px;height:103px;background:var(--blue);text-align:center;padding-top:16px}
  .attach-box a{font-weight:600;font-size:14px;color:var(--white);text-decoration:underline}
  .refresh{display:block;margin:15px auto 0;width:86px;height:34px;background:var(--yellow);border:0;color:var(--blue);font-family:"Open Sans",sans-serif;font-weight:600;font-size:14px}

  .section-title{font-family:"Roboto",sans-serif;font-size:18.5px;color:var(--blue);margin-top:20px;line-height:26px}
  .note{font-size:13px;line-height:21.6px;margin-top:6px}
  .note-strong{font-family:"Roboto",sans-serif;font-size:14.8px;margin-top:7px;line-height:22px}
  .alert{font-family:"Roboto",sans-serif;font-size:14.6px;color:var(--blue);margin-top:13px;line-height:22px}

  .radio-row{display:flex;align-items:center;margin-top:22px;font-family:"Open Sans",sans-serif;font-size:14px}
  .radio{display:flex;align-items:center;margin-right:26px}
  .radio span.dot{width:14px;height:14px;border-radius:50%;border:1px solid #a9a9a9;background:linear-gradient(#f4f4f4,#dedede);margin-right:9px}

  .field-grid{display:grid;grid-template-columns:195px 195px 195px;column-gap:30px;row-gap:0;margin-top:29px}
  .field label{display:block;font-family:"Roboto",sans-serif;font-size:13px;line-height:16px}
  .field .input{height:32px;border:1px solid #aaa;margin-top:12px;margin-bottom:17px;background:var(--white)}

  .type-row{display:flex;align-items:center;margin-top:19px;font-size:14px}
  .type-row .radio{margin-right:26px}
  .amount{display:flex;align-items:center;margin-left:42px;font-family:"Roboto",sans-serif;font-size:13px}
  .amount .input{width:70px;height:32px;border:1px solid #aaa;margin:0 7px 0 8px;padding:7px 6px;font-family:"Open Sans",sans-serif;font-size:13px;color:#444}

  .sign-title{font-family:"Roboto",sans-serif;font-size:14.8px;color:var(--blue);margin-top:28px;line-height:22px}
  .consent{font-size:12.6px;line-height:21.6px;text-align:justify;margin-top:6px}

  .site-footer{position:absolute;left:0;top:1152px;width:1165px;height:48px;background:var(--blue);color:var(--white);font-weight:600;font-size:14.3px;text-align:center;line-height:48px}
</style>
</head>
<body>

<header class="site-header">
  <div class="brand">
    <span class="brand-dot"></span>
    <span class="brand-name">SENTINEL WATCH<br>SERVICES</span>
  </div>
  <nav class="top-nav">
    <span>Home</span><span class="sep">|</span><span>Help</span>
    <span class="user">Dana Mercer</span>
    <span class="power"><svg width="14" height="14" viewBox="0 0 14 14" fill="none" stroke="#fff" stroke-width="1.8" stroke-linecap="round"><path d="M4.2 3.3a5 5 0 1 0 5.6 0"/><path d="M7 1.5v5"/></svg></span>
  </nav>
</header>

<nav class="side-nav">
  <a class="back" href="#"><svg width="16" height="14" viewBox="0 0 16 14"><path d="M7 1 1 7l6 6M1.5 7H15" fill="none" stroke="#2c63ad" stroke-width="2.6" stroke-linecap="round" stroke-linejoin="round"/></svg>BACK TO PROFILE</a>
  <a href="#"><span class="nav-icon"><svg width="18" height="12" viewBox="0 0 18 12"><rect x="1" y="1" width="16" height="10" fill="none" stroke="#2c63ad" stroke-width="2"/><circle cx="9" cy="6" r="2.3" fill="#2c63ad"/></svg></span>Direct Deposit</a>
  <a href="#"><span class="nav-icon"><svg width="16" height="14" viewBox="0 0 16 14" fill="none" stroke="#2c63ad" stroke-width="2" stroke-linecap="round"><path d="M1 3h3l7 8h3M1 11h3l7-8h3"/><path d="M12 1l2 2-2 2M12 9l2 2-2 2"/></svg></span>Change W-4</a>
  <a href="#"><span class="nav-icon"><svg width="16" height="16" viewBox="0 0 16 16" fill="none" stroke="#2c63ad" stroke-width="1.8"><path d="M8 1l6.5 3.7v6.6L8 15l-6.5-3.7V4.7z"/><path d="M8 1v14M1.5 4.7 14.5 11.3M14.5 4.7 1.5 11.3"/></svg></span>Labour Code</a>
  <a href="#"><span class="nav-icon"><svg width="8" height="15" viewBox="0 0 8 15" fill="#2c63ad"><circle cx="4.5" cy="2" r="2"/><path d="M1 6h5v7h2v2H0v-2h2V8H1z"/></svg></span>Personal Information</a>
  <a href="#"><span class="nav-icon"><svg width="18" height="12" viewBox="0 0 18 12"><path d="M1 6c2.5-4.5 13.5-4.5 16 0-2.5 4.5-13.5 4.5-16 0z" fill="#2c63ad"/><circle cx="9" cy="6" r="2.5" fill="#f7df73"/></svg></span>Appraisal and Review</a>
  <a href="#"><span class="nav-icon"><svg width="16" height="16" viewBox="0 0 16 16" fill="none" stroke="#2c63ad" stroke-width="1.8" stroke-linejoin="round"><path d="M12 9v5H2V4h5"/><path d="M6 10l1-3 6-6 2 2-6 6z"/></svg></span>Write Up-Slip</a>
  <a href="#"><span class="nav-icon"><svg width="14" height="16" viewBox="0 0 14 16" fill="#2c63ad"><path d="M3 5a4 4 0 0 1 8 0v1H3z"/><rect x="2" y="6" width="10" height="1.5"/><circle cx="7" cy="9.5" r="2.2"/><path d="M1 16c0-3 2.5-4.5 6-4.5s6 1.5 6 4.5z"/></svg></span>Employee Performance</a>
</nav>

<main class="form-panel">
  <div class="form-body">
    <h1 class="form-title">Employee Direct Deposit Enrollment Form</h1>
    <div class="title-rule"></div>
    <p class="intro">To enroll in Direct Deposit, simply fill out this form. Attach a voided check for each checking account - not a deposit slip. If depositing to a savings account, ask your bank to give you the Routing/Transit Number for your account. It isn't always, the same as the number on a swings deposit slip. This will help ensure that are paid correctly. Once filled out, accounting will revie,our information for processing. Once processed, you will receive an email confirmation with details.</p>
    <p class="intro">Employees must attach a voided check for each of their accounts to help verify their account numbers and bank routing numbers.</p>

    <div class="attach-box">
      <a href="#">Attach A Voided Check Or Bank Deposit Form for the Account</a>
      <button class="refresh">Refresh</button>
    </div>

    <h2 class="section-title">Account Information:</h2>
    <p class="note">The last item must be for the remaining amount owed to you. To distribute to more accounts, please complete another form.</p>
    <p class="note-strong">Make sure to indicate what kind of account, along with enrolling or declining.</p>
    <p class="alert">**Notify payroll immediately if you close or change bank account**</p>

    <div class="radio-row">
      <span class="radio"><span class="dot"></span>New Enrollment</span>
      <span class="radio"><span class="dot"></span>Change Enrollment</span>
      <span class="radio"><span class="dot"></span>Cancel Enrollment</span>
    </div>

    <div class="field-grid">
      <div class="field"><label>Bank Name:</label><div class="input"></div></div>
      <div class="field"><label>City:</label><div class="input"></div></div>
      <div class="field"><label>State:</label><div class="input"></div></div>
      <div class="field"><label>Routing Transit:</label><div class="input"></div></div>
      <div class="field"><label>Account Number:</label><div class="input"></div></div>
    </div>

    <div class="type-row">
      <span class="radio"><span class="dot"></span>Checking</span>
      <span class="radio"><span class="dot"></span>Savings</span>
      <span class="amount">Amount:<span class="input">100</span>%</span>
    </div>

    <h3 class="sign-title">Important! Please read and sign before completing and submitting.</h3>
    <p class="consent">I hereby authorize SENTINEL WATCH SERVICES to deposit any amounts owed me, as instructed by my employer, by initiating credit entries to my account at the financial institution (hereinafter "Bank.) indicated on this form. Further, I authorize Bank to accept and to credit any credit entries indicated by SENTINEL WATCH SERVICES to my account In the even that SENTINEL WATCH SERVICES deposits funds erroneously into my account, I authorize SENTINEL WATCH SERVICES to debit my account for an amount not to exceed the original amount of the erroneous credit.</p>
  </div>
  <div class="scrollbar"><span class="up"></span><span class="thumb"></span><span class="down"></span></div>
</main>

<footer class="site-footer">Copyright © 2016 Sentinel Watch Services. All Right Reserved</footer>

</body>
</html>
```